Business Card and Simple Logo Desgin

New Zealand based start up company "Vesta Advisory LTD" requires business cards and simple logo design.

Card Content.

Vesta Advisory LTD

Rebecca Thornbury
CA, BMS (Hons)

r.thornbury@vestaadvisory.co.nz
PH +64 21 574 613

Target Market(s)

Corporate Business in IT, Finance and accounting.

Industry/Entity Type

Business

```html
<!DOCTYPE html>
<html lang="en">
<head>
<meta charset="utf-8">
<title>Vesta Advisory LTD – Business Card</title>
<link rel="stylesheet" href="https://fonts.googleapis.com/css2?family=Open+Sans:wght@400;600;700&display=swap">
<style>
  :root {
    --page-bg: #2b2b2b;
    --card-bg: #f4f5f6;
    --card-shade: #e2e4e6;
    --brand-blue: #33bde9;
    --brand-green: #168a3e;
    --ink: #5a5d60;
    --ink-dark: #3d4043;
    --white: #ffffff;
  }
  * { box-sizing: border-box; margin: 0; padding: 0; }
  html, body { width: 1200px; height: 900px; overflow: hidden; }
  body {
    background: var(--page-bg);
    font-family: "Open Sans", sans-serif;
    position: relative;
  }
  .card {
    position: absolute;
    left: 240px;
    width: 720px;
    height: 400px;
    border-radius: 18px;
    background: linear-gradient(160deg, var(--white) 0%, var(--card-bg) 55%, var(--card-shade) 100%);
    overflow: hidden;
  }
  .card--front { top: 30px; }
  .card--back { top: 470px; }

  /* Front */
  .mark-dot {
    position: absolute;
    left: 58px; top: 72px;
    width: 56px; height: 56px;
    border-radius: 50%;
    background: var(--brand-green);
  }
  .name-band {
    position: absolute;
    left: 150px; top: 76px;
    width: 570px; height: 48px;
    border-radius: 24px 0 0 24px;
    background: var(--brand-blue);
    display: flex; align-items: center;
    padding-left: 30px;
  }
  .wordmark {
    font-weight: 700;
    font-size: 26px;
    color: var(--white);
    letter-spacing: 0.2px;
  }
  .person {
    position: absolute;
    left: 58px; top: 178px;
    color: var(--ink);
  }
  .person__name { font-size: 32px; font-weight: 400; line-height: 1.1; }
  .person__credentials { font-size: 19px; margin-top: 6px; }
  .rule-bar {
    position: absolute;
    left: 58px; right: 0; top: 270px;
    height: 14px;
    border-radius: 7px 0 0 7px;
    background: var(--brand-green);
  }
  .contact {
    position: absolute;
    left: 58px; top: 298px;
    color: var(--ink-dark);
    font-size: 20px;
    line-height: 1.65;
  }

  /* Back */
  .back-brand {
    position: absolute;
    inset: 0;
    display: flex; align-items: center; justify-content: center;
    gap: 22px;
  }
  .back-brand__dot {
    width: 70px; height: 70px;
    border-radius: 50%;
    background: var(--brand-green);
  }
  .back-brand__name {
    font-weight: 700;
    font-size: 38px;
    color: var(--brand-green);
  }
</style>
</head>
<body>
  <section class="card card--front" aria-label="Business card front">
    <div class="mark-dot" aria-hidden="true"></div>
    <div class="name-band"><span class="wordmark">Vesta Advisory LTD</span></div>
    <div class="person">
      <p class="person__name">Rebecca Thornbury</p>
      <p class="person__credentials">CA, BMS (Hons)</p>
    </div>
    <div class="rule-bar" aria-hidden="true"></div>
    <div class="contact">
      <p class="contact__phone">PH +64 21 574 613</p>
      <p class="contact__email">r.thornbury@vestaadvisory.co.nz</p>
    </div>
  </section>

  <section class="card card--back" aria-label="Business card back">
    <div class="back-brand">
      <div class="back-brand__dot" aria-hidden="true"></div>
      <span class="back-brand__name">Vesta Advisory LTD</span>
    </div>
  </section>
</body>
</html>
```